4th Generation Family Business Needs a New Card Design!

We are a family owned 4th Generation company. We are based in the Sydney, Australia area and we are desperately in need of a more modern and classy card. We are monumental masons who design, supply & erect lasting memorials throughout cemeteries in Sydney. Our customers are normally in a period of grieving. I have attached logo files that will need to be implemented on the card. Company was established 1935. Australian Owned and Operated. Card needs to be designed to PIXO.com specification.

Target Market(s)

Our target market is based upon people that a grieving for family members that have passed away. We also deal with alot of companies that own and operate cemeteries.

Industry/Entity Type

Business

Contact Information for Business Card

Simon Harcourt, Operations Manager, 0417293086, simon@harcourtmemorials.com.au
Lewis Harcourt, Director, 0491630572, lewis@harcourtmemorials.com.au
Phone # 02 9561 3048
Website: www.harcourtmemorials.com.au
Address: Suite 17, 8 Palfrey Lane, West Carlow, Sydney NSW 2156

Font styles to use
Serif
Decorative
Script

Requirements
Must have
• Would like to see the logo nicely implemented with a modern design. Embossed lettering would be a nice additive.

```html
<!DOCTYPE html>
<html lang="en">
<head>
<meta charset="utf-8">
<title>Harcourt Memorials – Business Card</title>
<link rel="stylesheet" href="https://fonts.googleapis.com/css2?family=Source+Sans+3:wght@400;600&family=Cormorant+Garamond:ital,wght@1,500&display=swap">
<style>
  :root {
    --backdrop: #8f9193;
    --paper: #f4f4f4;
    --ink: #1f1f1f;
    --ink-soft: #3a3a3a;
    --gold: #c9a227;
    --rule: #8a8a8a;
    --card-dark: #211f1f;
    --type-light: #e8e8e8;
  }
  * { box-sizing: border-box; margin: 0; padding: 0; }
  html, body { width: 1105px; height: 1200px; overflow: hidden; }
  body {
    background: var(--backdrop);
    font-family: "Source Sans 3", "Helvetica Neue", Arial, sans-serif;
    position: relative;
  }
  .card {
    position: absolute;
    left: 172px;
    width: 760px;
    height: 434px;
    overflow: hidden;
  }
  .card--front { top: 110px; background: var(--paper); color: var(--ink); }
  .card--back { top: 650px; background: var(--card-dark); }

  .brand {
    position: absolute;
    right: 32px;
    top: 62px;
    width: 230px;
    text-align: center;
    font-weight: 600;
    color: var(--ink);
    letter-spacing: 3px;
    line-height: 1.05;
  }
  .brand__name { font-size: 34px; display: block; }
  .brand__sub { font-size: 20px; display: block; letter-spacing: 5px; }

  .person { position: absolute; left: 39px; top: 200px; }
  .person__name { font-size: 27px; font-weight: 600; color: var(--ink); }
  .person__role { font-size: 21px; color: var(--gold); margin-top: 2px; }

  .divider {
    position: absolute; left: 39px; right: 32px; top: 269px;
    height: 2px; background: var(--rule);
  }

  .contacts { position: absolute; left: 39px; top: 282px; list-style: none; }
  .contacts li {
    display: flex; align-items: center; gap: 12px;
    font-size: 19px; color: var(--ink-soft); height: 29.5px;
  }
  .contacts svg { width: 16px; height: 16px; fill: var(--ink); flex: none; }

  .address {
    position: absolute; right: 32px; top: 312px;
    text-align: right; font-size: 19px; color: var(--ink-soft); line-height: 29.5px;
  }

  .base-band {
    position: absolute; left: 0; right: 0; bottom: 0; height: 14px; background: var(--ink);
  }
  .web-band {
    position: absolute; right: 0; bottom: 0; width: 370px; height: 40px;
    background: var(--gold);
    clip-path: polygon(28px 0, 100% 0, 100% 100%, 0 100%);
  }
  .web-band__url {
    position: absolute; right: 32px; bottom: 8px;
    font-size: 19px; color: var(--ink);
  }

  .back-brand {
    position: absolute; right: 40px; top: 268px;
    width: 270px; text-align: center;
    font-weight: 600; color: var(--type-light);
    letter-spacing: 3px; line-height: 1.05;
  }
  .back-brand .brand__name { font-size: 38px; }
  .back-brand .brand__sub { font-size: 22px; }
  .back-url {
    position: absolute; right: 40px; top: 362px; width: 270px; text-align: center;
    font-family: "Cormorant Garamond", Georgia, serif;
    font-style: italic; font-weight: 500; font-size: 24px; color: var(--type-light);
  }
</style>
</head>
<body>
  <section class="card card--front">
    <div class="brand">
      <span class="brand__name">HARCOURT</span>
      <span class="brand__sub">MEMORIALS</span>
    </div>

    <div class="person">
      <div class="person__name">Simon Harcourt</div>
      <div class="person__role">Operations Manager</div>
    </div>

    <div class="divider"></div>

    <ul class="contacts">
      <li>
        <svg viewBox="0 0 16 16" aria-hidden="true"><path d="M3.6 1.2l2.3 2.6-1.3 2a9 9 0 0 0 5.6 5.6l2-1.3 2.6 2.3-1.6 2.4C7.6 14.5 1.5 8.4 1.2 2.8z"/></svg>
        02 9561 3048
      </li>
      <li>
        <svg viewBox="0 0 16 16" aria-hidden="true"><path d="M4.5 0h7A1.5 1.5 0 0 1 13 1.5v13a1.5 1.5 0 0 1-1.5 1.5h-7A1.5 1.5 0 0 1 3 14.5v-13A1.5 1.5 0 0 1 4.5 0zM5 2v10.5h6V2zm3 11.2a.9.9 0 1 0 0 1.8.9.9 0 0 0 0-1.8z"/></svg>
        0417293086
      </li>
      <li>
        <svg viewBox="0 0 16 16" aria-hidden="true"><path d="M1 3h14v10H1zm1.5 1.3V5l5.5 3.6L13.5 5v-.7zM2.5 6.6v5.1h11V6.6L8 10.2z"/></svg>
        simon@harcourtmemorials.com.au
      </li>
    </ul>

    <div class="address">
      Suite 17, 8 Palfrey Lane<br>
      West Carlow, Sydney NSW 2156
    </div>

    <div class="base-band"></div>
    <div class="web-band"></div>
    <div class="web-band__url">www.harcourtmemorials.com.au</div>
  </section>

  <section class="card card--back">
    <div class="back-brand">
      <span class="brand__name">HARCOURT</span>
      <span class="brand__sub">MEMORIALS</span>
    </div>
    <div class="back-url">harcourtmemorials.com.au</div>
  </section>
</body>
</html>
```